Dental specialist needs a sharp looking letterhead

I am looking for a letterhead to be used to send letters and communication between myself (a dental specialist) and other dentists.
My office is a state of the art dental specialty office.
I need to letterhead to also state:
Bertram L. Oswick DDS
2748 Tollard Avenue, Suite K
West Tollard, NY 14391
(716)392-5061
fax: (716)392-5087
oswickroot.com (**this email address may change)

i included my logo designs.
thank you

Target Market(s)

dentists

Industry/Entity Type

Communication

Requirements
Must have
• the included logo, whether the vertical or horizontal versions

```html
<!DOCTYPE html>
<html lang="en">
<head>
<meta charset="utf-8">
<title>Meridian Endodontics P.C. – Letterhead</title>
<link rel="stylesheet" href="https://fonts.googleapis.com/css2?family=Roboto+Slab:wght@300;400;700&display=swap">
<style>
  :root {
    --paper: #ffffff;
    --ink: #111111;
    --ink-soft: #3a3a3a;
    --rule: #555555;
    --brand-blue: #3fa5de;
    --brand-green: #8cc63f;
    --on-green: #ffffff;
  }
  * { margin: 0; padding: 0; box-sizing: border-box; }
  html, body {
    width: 931px; height: 1200px; overflow: hidden;
    background: var(--paper);
  }
  .letterhead {
    position: relative;
    width: 931px; height: 1200px;
    background: var(--paper);
    font-family: "Roboto Slab", serif;
    color: var(--ink);
  }
  .brand {
    position: absolute; left: 32px; top: 34px;
    display: flex; align-items: center; height: 94px;
  }
  .brand-dot {
    width: 70px; height: 70px; border-radius: 50%;
    background: var(--brand-blue);
    margin-right: 14px;
  }
  .brand-divider {
    width: 1px; height: 94px; background: var(--rule);
    margin-right: 8px;
  }
  .brand-name {
    font-weight: 700; color: var(--ink);
    line-height: 1;
  }
  .brand-name .primary { display: block; font-size: 34px; letter-spacing: -0.5px; }
  .brand-name .secondary { display: block; font-size: 13px; letter-spacing: 2.2px; margin-top: 7px; padding-left: 28px; }

  .contact {
    position: absolute; left: 662px; top: 32px;
    border-left: 1px solid var(--rule);
    padding-left: 12px; height: 95px;
  }
  .contact-name {
    font-weight: 300; font-size: 20px; color: var(--ink-soft);
    line-height: 1; margin-top: 2px; margin-bottom: 9px;
  }
  .contact-line {
    display: flex; align-items: center;
    font-size: 15.5px; font-weight: 300; color: var(--ink-soft);
    line-height: 21px;
  }
  .contact-line svg { width: 14px; height: 14px; margin-right: 5px; flex: none; }

  .footer-rule {
    position: absolute; left: 0; width: 931px; height: 3px;
    background: var(--brand-blue);
  }
  .footer-rule.top { top: 1116px; }
  .footer-rule.bottom { top: 1172px; }
  .footer-band {
    position: absolute; left: 0; top: 1123px; width: 931px; height: 46px;
    background: var(--brand-green);
    display: flex; align-items: center; justify-content: center;
    color: var(--on-green); font-size: 18.5px; font-weight: 400;
  }
  .footer-band svg { width: 14px; height: 18px; margin-right: 12px; }
</style>
</head>
<body>
  <main class="letterhead">
    <header>
      <div class="brand">
        <span class="brand-dot" aria-hidden="true"></span>
        <span class="brand-divider" aria-hidden="true"></span>
        <div class="brand-name">
          <span class="primary">MERIDIAN</span>
          <span class="secondary">Endodontics P.C.</span>
        </div>
      </div>

      <address class="contact">
        <p class="contact-name">Bertram L. Oswick, DDS</p>
        <p class="contact-line">
          <svg viewBox="0 0 16 16" aria-label="Phone"><circle cx="8" cy="8" r="7" fill="none" stroke="var(--brand-blue)" stroke-width="1.4"/><path d="M6 4.5c-1 1-1 4 1 6s3.5 1.5 3.5 1.5l.5-1.2-1.6-1-.8.6c-.8-.5-1.6-1.5-2-2.3l.6-.8-.9-1.7z" fill="var(--brand-blue)"/></svg>
          716-392-5061
        </p>
        <p class="contact-line">
          <svg viewBox="0 0 16 16" aria-label="Fax"><rect x="4" y="2" width="8" height="5" fill="var(--brand-green)"/><rect x="1" y="7" width="14" height="6" rx="1.5" fill="var(--brand-green)"/><rect x="4" y="10" width="8" height="4" fill="#fff"/></svg>
          716-392-5087
        </p>
        <p class="contact-line">
          <svg viewBox="0 0 16 16" aria-label="Email"><rect x="1" y="3.5" width="14" height="9" fill="var(--brand-blue)"/><path d="M1 3.5l7 5 7-5" fill="none" stroke="#fff" stroke-width="1.2"/></svg>
          office@oswickroot.com
        </p>
      </address>
    </header>

    <footer>
      <div class="footer-rule top"></div>
      <div class="footer-band">
        <svg viewBox="0 0 14 18" aria-label="Location"><path d="M7 0C3.1 0 0 3 0 6.8 0 11.5 7 18 7 18s7-6.5 7-11.2C14 3 10.9 0 7 0z" fill="var(--on-green)"/><circle cx="7" cy="6.8" r="2.6" fill="var(--brand-green)"/></svg>
        2748 Tollard Avenue, Suite K, West Tollard, NY 14391
      </div>
      <div class="footer-rule bottom"></div>
    </footer>
  </main>
</body>
</html>
```